International Clinical Software Company needs a new business card design

We are looking for a new business card design for our company that has recently expanded into the UK market, making us a multinational company.
After having rebranded our website and produced a new style guide, we are looking for a business card that is creative and attention grabbing, while being consistent with the style and colour scheme used on the new website, www.plumvora.example
We produce care management technology for the aged care market, but the main aspect we aim to communicate is the human element of our software, and the way it assists in providing better care for aged people, and stronger relationships between aged people and the staff that care for them.
Our current business card is a dark green with gold text, which makes the text quite difficult to read, not very aesthetically appealing and the colour scheme looks quite dated.
We would like something fresh and modern, that can still be colourful but doesn't use large blocks of dark colour, and uses the colours within our logo.
Something tying in with the leaves that are used in our logo could work quite nicely, along with the Autumn/Fall colours of soft greens, yellows and reds (also in our existing logo). However also happy to look at fresh, completely out of the box ideas we may not have yet considered.
Target Market(s)
The people that receive this business card work in the aged card or health industry and are either corporate/management level staff or clinical (Registered Nurses, care workers etc.)
Industry/Entity Type
Health Product
Contact Information for Business Card
Company Name - BrindlewayCare
Company locations: United Kingdom, Australia, New Zealand
Staff Details:
Staff name: Derek Mallow
Staff job title: Executive Chairman
Staff email: d.mallow@plumvora.example
Office phone number: 01742 918576
Font styles to use
Other font styles liked:
- Calibri
Requirements
Must have
- Must include the BrindlewayCare brand name in it's current font
- Must include logo (3 leaves in gold circle)
- Must include Business Card Details
Nice to have
- Elements of gold
- White space
- Something autumn themed but not too cliched
Should not have
- No blue - used by a major competitor and we would like to differentiate from them
- Large blocks of dark green colour (the green that appears in our leaves on the logo on our current business card is the background colour and it is far too dark)

```html
<!DOCTYPE html>
<html lang="en">
<head>
<meta charset="utf-8">
<title>BrindlewayCare – Business Card</title>
<link href="https://fonts.googleapis.com/css2?family=Carlito:wght@400;700&display=swap" rel="stylesheet">
<style>
  :root {
    --page-bg: #e4e0da;
    --card-bg: #f3f2ef;
    --card-edge: #d9d6d0;
    --brand-gold: #8a7650;
    --logo-gold: #b89a5a;
    --name-brown: #8a7a58;
    --title-maroon: #8e1f3c;
    --body-grey: #4a4744;
    --icon-grey: #6b6762;
    --leaf-green: #8fb07a;
    --leaf-yellow: #d3c85a;
    --leaf-red: #b8434a;
  }
  * { margin: 0; padding: 0; box-sizing: border-box; }
  html, body {
    width: 1200px; height: 969px; overflow: hidden;
    background: var(--page-bg);
    font-family: "Carlito", "Calibri", sans-serif;
  }
  .business-card {
    position: absolute; left: 100px; top: 200px;
    width: 1000px; height: 569px;
    background: var(--card-bg);
    border: 1px solid var(--card-edge);
    border-radius: 30px;
    overflow: hidden;
    box-shadow: 0 10px 30px rgba(0,0,0,0.12);
  }
  .brand-mark {
    position: absolute; left: 153px; top: 46px;
    width: 104px; height: 104px;
    border-radius: 50%;
    border: 4px solid var(--logo-gold);
  }
  .brand-name {
    position: absolute; left: 52px; top: 168px;
    font-size: 56px; font-weight: 400;
    color: var(--brand-gold);
    letter-spacing: 1px;
  }
  .person-name {
    position: absolute; left: 52px; top: 250px;
    font-size: 35px; font-weight: 700;
    color: var(--name-brown);
  }
  .person-title {
    position: absolute; left: 52px; top: 290px;
    font-size: 29px; font-weight: 400;
    color: var(--title-maroon);
  }
  .locations {
    position: absolute; left: 52px; top: 334px;
    font-size: 27px; line-height: 35px;
    color: var(--body-grey);
  }
  .contact-list {
    position: absolute; left: 52px; top: 414px;
    list-style: none;
    font-size: 26px; line-height: 38px;
    color: var(--body-grey);
  }
  .contact-list li { display: flex; align-items: center; gap: 14px; }
  .contact-list svg { width: 24px; height: 24px; fill: var(--icon-grey); flex: none; }
  .leaf-artwork {
    position: absolute; left: 620px; top: 0;
    width: 380px; height: 569px;
  }
</style>
</head>
<body>
  <section class="business-card">
    <div class="brand-mark"></div>
    <div class="brand-name">BrindlewayCare</div>

    <div class="person-name">Derek Mallow</div>
    <div class="person-title">Executive Chairman</div>

    <div class="locations">
      United Kingdom<br>
      Australia • New Zealand
    </div>

    <ul class="contact-list">
      <li>
        <svg viewBox="0 0 24 24" aria-hidden="true"><path d="M6.6 10.8a15.1 15.1 0 0 0 6.6 6.6l2.2-2.2a1 1 0 0 1 1-.25 11.4 11.4 0 0 0 3.6.57 1 1 0 0 1 1 1V20a1 1 0 0 1-1 1A17 17 0 0 1 3 4a1 1 0 0 1 1-1h3.5a1 1 0 0 1 1 1c0 1.25.2 2.45.57 3.57a1 1 0 0 1-.25 1z"/></svg>
        01742 918576
      </li>
      <li>
        <svg viewBox="0 0 24 24" aria-hidden="true"><path d="M2 5h20v14H2z M3.5 6.5 12 12.5l8.5-6z" fill-rule="evenodd"/></svg>
        d.mallow@plumvora.example
      </li>
      <li>
        <svg viewBox="0 0 24 24" aria-hidden="true"><circle cx="12" cy="12" r="10"/><path d="M2 12h20M12 2c3 3 3 17 0 20M12 2c-3 3-3 17 0 20" stroke="#f3f2ef" stroke-width="1.5" fill="none"/></svg>
        www.plumvora.example
      </li>
    </ul>

    <svg class="leaf-artwork" viewBox="0 0 380 569" role="img" aria-label="Illustration of three overlapping autumn leaves in green, yellow and red rising from the lower right of the card">
      <defs>
        <linearGradient id="leafTones" x1="0.3" y1="0" x2="0.6" y2="1">
          <stop offset="0" stop-color="var(--leaf-green)" stop-opacity="0.55"/>
          <stop offset="0.5" stop-color="var(--leaf-yellow)" stop-opacity="0.6"/>
          <stop offset="1" stop-color="var(--leaf-red)" stop-opacity="0.6"/>
        </linearGradient>
      </defs>
      <rect x="0" y="0" width="380" height="569" fill="url(#leafTones)"/>
    </svg>
  </section>
</body>
</html>
```